Logo, Web and Mobile Designs for enterprise social media platform

All the details are in the attached document, please start reading the scope document first which explains what is this project about and the details about the needed deliverables, after that please read the UI_Requirements document which will detail what is expected regarding the coded web version since this is a coded contest, it is very important that you meet the UI requirements or suggest something else but we will need to agree first before working on the coded version

Good Luck

Target Market(s)

Enterprise Social Media

Industry/Entity Type

Media

Coding

Coded - Design and coding required

Number of Pages Required

5+ page

Font styles to use
Sans Serif

Requirements
Must have
• All the must haves are listed in the scope document so please check before you start

```html
<!DOCTYPE html>
<html lang="en">
<head>
<meta charset="utf-8">
<title>Taskora – Create New Business Opportunity</title>
<link href="https://fonts.googleapis.com/css2?family=Open+Sans:wght@400;600&family=Roboto:wght@400;500&family=Roboto+Condensed:wght@400&display=swap" rel="stylesheet">
<style>
  :root{
    --page-bg:#f8f8f8;
    --header-bg:#fafafa;
    --line:#e2e2e2;
    --field-line:#dcdcdc;
    --card-head:#f5f6f8;
    --text:#5f5f5f;
    --title:#5a5d66;
    --icon:#777;
    --brand:#2a9fd3;
    --brand-dot:#f39c12;
    --accent:#e8900a;
    --accent-dark:#c77a06;
    --footer:#1f8db8;
    --white:#fff;
  }
  *{box-sizing:border-box;margin:0;padding:0}
  html,body{width:1200px;height:2445px;overflow:hidden}
  body{background:var(--page-bg);font-family:"Roboto",Arial,sans-serif;color:var(--text);position:relative}

  .site-header{position:absolute;left:0;top:0;width:1200px;height:235px;
    background:linear-gradient(#fdfdfd,#f3f3f3);border-bottom:3px solid var(--line)}
  .header-divider{position:absolute;top:0;width:2px;height:232px;background:var(--line)}
  .header-divider.left{left:215px}
  .header-divider.right{left:992px}
  .home-icon{position:absolute;left:76px;top:94px}
  .menu-icon{position:absolute;left:1072px;top:96px}
  .brand{position:absolute;left:345px;top:70px;display:flex;align-items:center;gap:20px}
  .brand-dot{width:82px;height:82px;border-radius:50%;background:var(--brand-dot)}
  .brand-name{font-family:"Open Sans",Arial,sans-serif;font-weight:600;font-size:74px;color:var(--brand);line-height:1}

  .card{position:absolute;left:43px;top:311px;width:1112px;height:1676px;background:var(--white);border:2px solid var(--line)}
  .card-head{height:142px;background:var(--card-head);border-bottom:2px solid var(--line);
    padding:58px 0 0 40px;font-size:35px;color:var(--title);letter-spacing:.3px}
  .field-label{position:absolute;left:68px;font-size:40px;color:var(--text)}
  .field{position:absolute;left:68px;width:970px;background:var(--white);border:2px solid var(--field-line);border-radius:8px;
    font-family:"Open Sans",Arial,sans-serif;font-size:35px;color:#555;padding-left:66px;display:flex;align-items:center}
  .field.select .chevron{position:absolute;right:0;top:0;width:112px;height:100%;border-left:2px solid var(--field-line);
    display:flex;align-items:center;justify-content:center}
  .radio-group{position:absolute;left:68px;top:1370px;display:flex;align-items:center;
    font-family:"Open Sans",Arial,sans-serif;font-size:35px;color:#555}
  .radio{width:42px;height:42px;border-radius:50%;border:2px solid #ddd;background:radial-gradient(#fff 40%,#e9e9e9);
    margin-right:30px;display:flex;align-items:center;justify-content:center}
  .radio.checked::after{content:"";width:14px;height:14px;border-radius:50%;background:#aaa}
  .radio-option{display:flex;align-items:center;margin-right:70px}
  .submit-btn{position:absolute;left:68px;top:1472px;width:685px;height:102px;background:var(--accent);border:none;border-radius:6px;
    box-shadow:0 6px 0 var(--accent-dark);color:var(--white);font-family:"Open Sans",Arial,sans-serif;font-weight:600;font-size:43px;text-transform:uppercase}

  .site-footer{position:absolute;left:0;top:2077px;width:1200px;height:368px;background:var(--footer);color:var(--white);text-align:center}
  .social{position:absolute;top:77px;left:0;width:1200px;display:flex;justify-content:center;gap:28px}
  .social span{width:60px;height:60px;border-radius:10px;background:var(--white)}
  .footer-nav{position:absolute;top:175px;width:1200px;font-family:"Roboto Condensed",Arial,sans-serif;font-size:37px;word-spacing:4px}
  .footer-nav .sep{margin:0 16px}
  .copyright{position:absolute;top:260px;width:1200px;font-family:"Roboto Condensed",Arial,sans-serif;font-size:34px}
</style>
</head>
<body>
  <header class="site-header">
    <svg class="home-icon" width="50" height="46" viewBox="0 0 50 46" aria-label="Home">
      <path d="M25 4 L2 24 L8 24 L8 44 L20 44 L20 31 L30 31 L30 44 L42 44 L42 24 L48 24 Z" fill="var(--icon)"/>
    </svg>
    <div class="header-divider left"></div>
    <div class="brand">
      <span class="brand-dot"></span>
      <span class="brand-name">Taskora</span>
    </div>
    <div class="header-divider right"></div>
    <svg class="menu-icon" width="50" height="44" viewBox="0 0 50 44" aria-label="Menu">
      <rect x="0" y="0" width="50" height="9" rx="2" fill="var(--icon)"/>
      <rect x="0" y="17" width="50" height="9" rx="2" fill="var(--icon)"/>
      <rect x="0" y="34" width="50" height="9" rx="2" fill="var(--icon)"/>
    </svg>
  </header>

  <main class="card">
    <div class="card-head">CREATE NEW BUSINESS OPPORTUNITY - STEP 1</div>

    <label class="field-label" style="top:195px">Name : *</label>
    <div class="field" style="top:261px;height:110px"></div>

    <label class="field-label" style="top:415px">Description : *</label>
    <div class="field" style="top:481px;height:365px"></div>

    <label class="field-label" style="top:898px">Choose Network : *</label>
    <div class="field select" style="top:965px;height:110px">Create New
      <span class="chevron">
        <svg width="26" height="16" viewBox="0 0 26 16"><path d="M3 3 L13 12 L23 3" fill="none" stroke="#666" stroke-width="3.5"/></svg>
      </span>
    </div>
    <div class="field" style="top:1097px;height:111px">Enter the new network name</div>

    <label class="field-label" style="top:1280px">Comments Visibility : *</label>
    <div class="radio-group">
      <div class="radio-option"><span class="radio"></span>Public</div>
      <div class="radio-option"><span class="radio checked"></span>Private</div>
    </div>

    <button class="submit-btn">Save and go to step 2</button>
  </main>

  <footer class="site-footer">
    <div class="social"><span></span><span></span><span></span><span></span><span></span></div>
    <nav class="footer-nav">Home<span class="sep">/</span>Contact<span class="sep">/</span>Topics<span class="sep">/</span>Posts &amp; Comments<span class="sep">/</span>Videos Links</nav>
    <p class="copyright">Copyright @ 2015 - 2015.Taskora. All Rights Reserved.</p>
  </footer>
</body>
</html>
```